Business Card Design Project

Business Card design based on logo.
Updates

I need business card, letterhead, envelope, and if possible, Powerpoint slide template.

On front of business card: Just logo- and  my name and title:  Harriet Lindqvist, Principal

On reverse-logo and the rest of the contact info:

4871 Quarry Lane
Davis, CA 95618
650-318-2764
hl@brackenstudyworks.example

On letterhead-Just logo at top, at bottom  the rest-very small along the bottom

On PPT slide-just the logo.

I also want to try a few other colors-I like lime/dark grey (not black) but would like to try Sienna, maybe also indigo or bright blue-green.

I forgot to add-

On the business card-switch to vertical on reverse side and put:

Reverse side-switch to vertical and list:

Harriet Lindqvist
Principal
Bracken Study Works, LLC

650-318-2764

4871 Quarry Lane
Davis, CA 95618

Harriet Lindqvist
Principal

650-318-2764

4871 Quarry Lane
Davis, CA 95618

I have another project at the same time-for Stationery. Feel free to submit to that one also.

That one includes letterhead, envelope, PPT slide, folder cover sheet-HL

Industry/Entity Type

Business

Requirements
Must have
• Must use logo-preferably lime green version-with gray, not black or just 2-tone -logo on colored background.

```html
<!DOCTYPE html>
<html lang="en">
<head>
<meta charset="utf-8">
<title>Bracken Study Works – Business Cards</title>
<link rel="stylesheet" href="https://fonts.googleapis.com/css2?family=Jost:wght@400;500&display=swap">
<style>
  :root {
    --lime: #97ba3f;
    --lime-faint: #f3f6ea;
    --slate: #4a4a4c;
    --paper: #ffffff;
    --backdrop: #6e4330;
    --card-edge: #8a8a8a;
  }
  * { box-sizing: border-box; margin: 0; padding: 0; }
  html, body { width: 1200px; height: 704px; overflow: hidden; }
  body {
    background: var(--backdrop);
    font-family: "Jost", "Futura", sans-serif;
    position: relative;
  }
  .card {
    position: absolute;
    width: 502px;
    height: 287px;
    border-radius: 22px;
    background: var(--paper);
    border: 1px solid var(--card-edge);
    overflow: hidden;
  }
  .card--front-contact { left: 84px; top: 43px; }
  .card--back-green { left: 622px; top: 55px; background: var(--lime); border-color: var(--lime); }
  .card--back-pattern { left: 89px; top: 369px; }
  .card--front-plain { left: 622px; top: 373px; }

  .brand {
    position: absolute;
    display: flex;
    align-items: center;
    gap: 10px;
    color: var(--slate);
    font-weight: 400;
    text-transform: uppercase;
    letter-spacing: 0.14em;
    white-space: nowrap;
    transform: translateX(-50%);
  }
  .brand__dot { width: 14px; height: 14px; background: var(--lime); flex: none; }
  .brand__name { line-height: 1; }

  .website {
    position: absolute;
    left: 0; right: 0;
    text-align: center;
    color: var(--slate);
    font-size: 19px;
    letter-spacing: 0.16em;
    white-space: nowrap;
  }

  /* card 1 */
  .card--front-contact .brand { left: 138px; top: 136px; font-size: 16px; letter-spacing: 0.12em; }
  .contact-strip {
    position: absolute;
    left: 284px; top: 41px;
    width: 22px; height: 212px;
    background: var(--slate);
  }
  .contact-strip__url {
    position: absolute;
    left: 50%; top: 50%;
    transform: translate(-50%, -50%) rotate(-90deg);
    color: var(--paper);
    font-size: 11.5px;
    letter-spacing: 0.04em;
    white-space: nowrap;
  }
  .contact-panel {
    position: absolute;
    left: 308px; top: 41px;
    width: 194px; height: 212px;
    background: var(--lime);
    color: var(--paper);
    padding: 20px 0 0 16px;
  }
  .contact-panel__name { font-size: 19px; font-weight: 500; line-height: 1.1; }
  .contact-panel__title { font-size: 15px; margin-top: 3px; margin-bottom: 8px; }
  .contact-list { list-style: none; font-size: 13px; line-height: 20px; }
  .contact-list li { display: flex; gap: 5px; align-items: flex-start; white-space: nowrap; }
  .contact-list li.gap { margin-top: 10px; }
  .contact-list svg { width: 11px; height: 11px; margin-top: 5px; flex: none; fill: var(--paper); }

  /* card 2 */
  .card--back-green .brand {
    left: 50%; top: 110px;
    color: var(--paper);
    font-size: 26px;
  }
  .card--back-green .brand__dot { background: var(--paper); width: 20px; height: 20px; }
  .card--back-green .website { top: 255px; color: var(--paper); }

  /* card 3 */
  .pattern-field {
    position: absolute;
    inset: 0;
    background: var(--lime-faint);
  }
  .card--back-pattern .brand { left: 50%; top: 130px; font-size: 30px; }
  .card--back-pattern .brand__dot { width: 22px; height: 22px; }
  .card--back-pattern .website { top: 256px; }

  /* card 4 */
  .card--front-plain .brand { left: 50%; top: 150px; font-size: 23px; }
  .card--front-plain .brand__dot { width: 18px; height: 18px; }
  .card--front-plain .website { top: 260px; }
</style>
</head>
<body>

  <section class="card card--front-contact">
    <div class="brand">
      <span class="brand__dot"></span>
      <span class="brand__name">Bracken Study Works</span>
    </div>
    <div class="contact-strip">
      <span class="contact-strip__url">www.brackenstudyworks.example</span>
    </div>
    <div class="contact-panel">
      <p class="contact-panel__name">Your Name</p>
      <p class="contact-panel__title">Title</p>
      <ul class="contact-list">
        <li>
          <svg viewBox="0 0 12 12"><path d="M2.5 1l2 2.2-1 1.3c.7 1.5 1.6 2.4 3 3l1.3-1 2.2 2-1 1.5C5.5 10 2 6.5 1 2.5z"/></svg>
          <span>0987 654321</span>
        </li>
        <li>
          <svg viewBox="0 0 12 12"><rect x="3" y="0.5" width="6" height="11" rx="1.2"/><rect x="4" y="2" width="4" height="6.5" fill="#97ba3f"/></svg>
          <span>0987 654321</span>
        </li>
        <li>
          <svg viewBox="0 0 12 12"><rect x="0.5" y="2.5" width="11" height="7.5" rx="1"/><path d="M1 3l5 4 5-4" stroke="#97ba3f" stroke-width="1" fill="none"/></svg>
          <span>info@bracken.example</span>
        </li>
        <li class="gap">
          <svg viewBox="0 0 12 12"><circle cx="6" cy="6" r="5.5"/><circle cx="6" cy="5" r="1.8" fill="#97ba3f"/></svg>
          <span>00, Complex name<br>City, State 0042</span>
        </li>
      </ul>
    </div>
  </section>

  <section class="card card--back-green">
    <div class="brand">
      <span class="brand__dot"></span>
      <span class="brand__name">Bracken Study Works</span>
    </div>
    <p class="website">www.brackenstudyworks.example</p>
  </section>

  <section class="card card--back-pattern">
    <div class="pattern-field" role="img" aria-label="Faint repeating brand pattern in pale lime"></div>
    <div class="brand">
      <span class="brand__dot"></span>
      <span class="brand__name">Bracken Study Works</span>
    </div>
    <p class="website">www.brackenstudyworks.example</p>
  </section>

  <section class="card card--front-plain">
    <div class="brand">
      <span class="brand__dot"></span>
      <span class="brand__name">Bracken Study Works</span>
    </div>
    <p class="website">www.brackenstudyworks.example</p>
  </section>

</body>
</html>
```